Business Card Design

Business Card for professional consulting firm working with large financial institutions.

Target Market(s)

Executive buyers

Industry/Entity Type

Banking

Contact Information for Business Card

Mild creativity wanted. Not boring, but do elaborate artwork.

Font styles to use
Serif
Sans Serif

Colors

Designer to choose colors to be used in the design.

Requirements
Must have
• Standard business card features - company name, individual name, telephone, website, email, locations.
Nice to have
• Two colors
Should not have
• too many colors, fancy printing, cartoons.

```html
<!DOCTYPE html>
<html lang="en">
<head>
<meta charset="utf-8">
<title>Northmere Business Card</title>
<link rel="stylesheet" href="https://fonts.googleapis.com/css2?family=Merriweather:wght@300&family=Montserrat:wght@600;700&display=swap">
<style>
  :root {
    --page: #ecebe8;
    --ink: #0b0b0b;
    --paper: #f7f7f7;
    --swoosh: #bdbdbd;
    --muted: #a9a9a9;
    --text: #4a4a4a;
  }
  * { margin: 0; padding: 0; box-sizing: border-box; }
  html, body { width: 1200px; height: 950px; overflow: hidden; background: var(--page); }
  .canvas { position: relative; width: 1200px; height: 950px; }
  .card { position: absolute; top: 142px; width: 380px; height: 665px; box-shadow: 0 12px 30px rgba(0,0,0,.25); }
  .card--front { left: 170px; }
  .card--back { left: 650px; background: var(--ink); }
  .card svg { position: absolute; inset: 0; display: block; }
  .front-content { position: absolute; left: 70px; top: 190px; width: 260px; }
  .brand { font-family: "Merriweather", serif; font-weight: 300; font-size: 38px; color: var(--ink); letter-spacing: .5px; }
  .person { margin-top: 22px; font-family: "Montserrat", sans-serif; }
  .person__name { font-weight: 700; font-size: 19px; color: var(--ink); letter-spacing: .5px; }
  .person__role { font-weight: 600; font-size: 15px; color: var(--muted); letter-spacing: 1px; }
  .contact { margin-top: 18px; font-family: "Montserrat", sans-serif; font-weight: 600; font-size: 14px; line-height: 1.45; color: var(--text); }
  .contact__group + .contact__group { margin-top: 14px; }
  .back-brand { position: absolute; left: 50%; top: 50%; transform: translate(-50%, -50%) rotate(90deg);
    font-family: "Merriweather", serif; font-weight: 300; font-size: 46px; color: var(--paper); white-space: nowrap; letter-spacing: .5px; }
</style>
</head>
<body>
<main class="canvas">
  <section class="card card--front">
    <svg width="380" height="665" viewBox="0 0 380 665" aria-hidden="true">
      <rect width="380" height="665" fill="var(--ink)"/>
      <path d="M0,70 C110,20 300,30 380,95 L380,580 C300,640 110,650 0,600 Z" fill="var(--paper)"/>
      <path d="M290,52 C340,62 372,80 380,95 L380,140 C370,110 340,80 290,52 Z" fill="var(--swoosh)"/>
      <path d="M0,600 C30,612 70,622 120,628 C70,612 30,590 10,560 L0,560 Z" fill="var(--swoosh)"/>
    </svg>
    <div class="front-content">
      <div class="brand">northmere</div>
      <div class="person">
        <div class="person__name">DANIEL REYES</div>
        <div class="person__role">CEO/FOUNDER</div>
      </div>
      <div class="contact">
        <div class="contact__group">
          <div>1420 Harbor Street</div>
          <div>Juneau, Alaska 99801</div>
        </div>
        <div class="contact__group">
          <div>P. 555 214 0937</div>
          <div>hello@northmere.com</div>
          <div>www.northmere.com</div>
        </div>
      </div>
    </div>
  </section>
  <section class="card card--back">
    <div class="back-brand">northmere</div>
  </section>
</main>
</body>
</html>
```